Business Cards for new orthopaedic surgery practice

My husband and I are starting our own orthopaedic surgery practice. We are looking for a business card that is uniform, but one will have my name/title and the other will have his. You can just create one design with my name on it for now. But when I choose your design as the winning design I will ask that you add another copy with his name/title.

We are looking for classy, simple, elite all in one. We like dark blues/a little gold/yellow. Something that goes with our logo. We want our logo incorporated. Here is all the info you need:
Business name: RV Bone & Vitality Center
Location: 38517 North Willowmere Ave
Coral Springs, FL 33071
Phone: 954-218-4063
Fax: 954-582-7341
Email: info@myrvbonecare.example

Names: Lydia Vance, M.D.
Board Certified Hand and Upper Extremity Surgeon

Ebo Dansu, M.D.
Board Certified Hip & Knee Replacement/General Orthopaedic Surgeon

Can decide what you want to put on the back. Maybe a slogan:
Rooted in Care. Focused on You

I am just going to upload our logo. The only thing is if we select you as the winning design, the location, and phone numbers may change. We will need your help to update that once fully solidified.

Industry/Entity Type

Medical

Contact Information for Business Card

Colors
0054AA
0677BA
7BADD7
CADEEF
E8F1F8
0094D4
00A9DD
6FCCEA
C7EBF8
E9F6FB

Requirements
Must have
• class, appeal,
Should not have
• We want to air on the side of masculine if we are looking at masculine vs. feminine feel. But we still want it classy, sophisticated, and something we will love

```html
<!DOCTYPE html>
<html lang="en">
<head>
<meta charset="utf-8">
<title>RV Bone &amp; Vitality Center – Business Card</title>
<link rel="stylesheet" href="https://fonts.googleapis.com/css2?family=PT+Serif:wght@400;700&display=swap">
<style>
  :root {
    --navy: #283f80;
    --cyan: #1ebfe6;
    --white: #ffffff;
    --backdrop: #f0f0f0;
  }
  * { box-sizing: border-box; margin: 0; padding: 0; }
  html, body {
    width: 1200px; height: 990px; overflow: hidden;
    background: var(--backdrop);
    font-family: "PT Serif", "Times New Roman", serif;
  }
  .card {
    position: absolute; left: 244px; width: 712px; height: 406px;
    overflow: hidden;
  }
  .card-front { top: 68px; background: var(--navy); }
  .card-back { top: 516px; background: var(--white); }

  /* front */
  .front-name {
    position: absolute; left: 0; right: 0; top: 150px;
    text-align: center; color: var(--white);
    font-size: 38px; line-height: 1.15; letter-spacing: 1px;
  }
  .slogan {
    position: absolute; left: 0; right: 0; top: 356px;
    display: flex; justify-content: center; gap: 12px;
    color: var(--white); font-size: 17px; letter-spacing: 0.5px;
  }
  .slogan span { display: flex; align-items: center; }
  .slogan span::before {
    content: ""; width: 7px; height: 7px; border-radius: 50%;
    background: var(--cyan); margin-right: 7px; margin-top: 3px;
  }

  /* back */
  .back-brand {
    position: absolute; left: 26px; top: 38px;
    color: var(--navy); font-size: 28px; line-height: 1.12;
    display: flex; align-items: center; gap: 14px;
  }
  .brand-mark { width: 16px; height: 16px; background: var(--navy); flex: none; }
  .doctor {
    position: absolute; right: 29px; top: 26px; text-align: right;
  }
  .doctor-name { color: var(--cyan); font-weight: 700; font-size: 24px; letter-spacing: 1px; }
  .doctor-title { color: var(--navy); font-size: 15px; line-height: 1.4; margin-top: 2px; letter-spacing: 0.3px; }
  .accent-tab {
    position: absolute; right: 0; top: 26px; width: 19px; height: 65px;
    background: var(--cyan);
  }
  .contact-band {
    position: absolute; left: 0; right: 0; top: 215px; bottom: 0;
    background: var(--navy);
  }
  .address {
    position: absolute; left: 22px; top: 14px;
    color: var(--cyan); font-size: 15px; line-height: 20px; letter-spacing: 0.3px;
  }
  .contact-list {
    position: absolute; left: 22px; top: 82px; list-style: none;
    color: var(--white); font-size: 15px; letter-spacing: 0.3px;
  }
  .contact-list li { display: flex; align-items: center; height: 20.5px; }
  .contact-list svg { width: 14px; height: 14px; margin-right: 9px; flex: none; }
  .band-brand {
    position: absolute; right: 24px; bottom: 26px; text-align: right;
    color: var(--white); font-size: 34px; line-height: 1.1;
  }
</style>
</head>
<body>
  <section class="card card-front">
    <div class="front-name">RV Bone &amp;<br>Vitality Center</div>
    <div class="slogan"><span>Rooted in Care</span><span>Focused on You</span></div>
  </section>

  <section class="card card-back">
    <div class="back-brand"><span class="brand-mark"></span><span>RV Bone &amp;<br>Vitality Center</span></div>

    <div class="doctor">
      <div class="doctor-name">Lydia Vance, M.D.</div>
      <div class="doctor-title">Board Certified Hand<br>and Upper Extremity Surgeon</div>
    </div>
    <div class="accent-tab"></div>

    <div class="contact-band">
      <div class="address">38517 North Willowmere Ave<br>Coral Springs, FL 33071</div>
      <ul class="contact-list">
        <li><svg viewBox="0 0 16 16" fill="none" stroke="#1ebfe6" stroke-width="1.6"><path d="M3 2h3l1 3-2 1.5a9 9 0 0 0 4.5 4.5L11 9l3 1v3a1.5 1.5 0 0 1-1.5 1.5A11.5 11.5 0 0 1 1.5 3.5 1.5 1.5 0 0 1 3 2z"/></svg>954-218-4063</li>
        <li><svg viewBox="0 0 16 16" fill="#1ebfe6"><rect x="1" y="5" width="3" height="10"/><rect x="5" y="6" width="10" height="9"/><rect x="7" y="1" width="6" height="5"/></svg>954-582-7341</li>
        <li><svg viewBox="0 0 16 16" fill="none" stroke="#1ebfe6" stroke-width="1.3"><circle cx="8" cy="8" r="6.5"/><ellipse cx="8" cy="8" rx="3" ry="6.5"/><path d="M1.5 8h13M2.5 4.5h11M2.5 11.5h11"/></svg>www.myrvbonecare.example</li>
        <li><svg viewBox="0 0 16 16" fill="none" stroke="#1ebfe6" stroke-width="1.4"><rect x="1" y="4" width="14" height="10"/><path d="M1 4l7 5 7-5"/></svg>info@myrvbonecare.example</li>
      </ul>
      <div class="band-brand">RV Bone &amp;<br>Vitality Center</div>
    </div>
  </section>
</body>
</html>
```